Label design - Superfood blend

We are a family owned nutrition company with big ambitions. Our goal is to develop a range of 100% natural supplements for women, inspired by nature & modern technology that helps them meet their nutritional needs while nourishing them from within. All our products are junk free because we believe that that’s how nature intended it. We also produce products through a sustainable process and only use biodegradable packaging for our products (See link - https://www.loamwrap.org.uk/biodegradable-stand-pouch-250g-kraft)

Our brand style is modern and minimalist. This same style will be reflected in our social media, website and we want it to be represented through the label designs for our product packaging.

We want some creative designers to design a label that is true to our style (See attached packaging brief with designs we like) and displays our values of Premium, High Quality, Organic Real Food supplements focused on women. I have provided examples in the attached brief, but please only use as inspiration, I dont want any of them to be copied (sorry have had my fingers burnt already !)
Updates

Hello all, Please note this design is for a LABEL and not the whole package. We will have a 500gm biodegradable brown package, and we will have a label (which is what this project is about) that will be stuck on the front. The size of the label will be a rectangle (unless you come up with a new shape) in the size 20cm * 15cm. Please do not submit designs for the WHOLE from of the package, as we dont intend to have printed packages. Regards

Hello all, I have added a new logo version to the attachments, could you please also try that version. Could you also please look at the new sliders. We are only looking for a minimlaist theme. If you dont know what that means, please do feel free to ask, I would be happy to supply examples. Minimalist designs, means clean, modern, upmarket, elegant designs. It does not use too many colors and mostly sticks to a combination of black and white with colors used sparingly. See some below for your reference anyway. https://www.pitchloft.co.uk/design/13359317 https://www.pitchloft.co.uk/design/17270649 https://www.pitchloft.co.uk/design/12584145 https://www.pitchloft.co.uk/design/12367479 https://www.snapquilt.com/search/pins/?q=minimalist%20label%20design&rs=rs&eq=&etslf=2809&term_meta[]=minimalist%7Crecentsearch%7Cundefined&term_meta[]=label%7Crecentsearch%7Cundefined&term_meta[]=design%7Crecentsearch%7Cundefined Regards

Target Market(s)

The target market is women between the age 25 to 45, based in UK (mostly based in larger cities in UK). They are typically middle class or higher and would be in demanding jobs and social lives, that requires for them to meet their nutrition needs in convenient, easy to take forms. The women would also be socially conscious and sensitive to issues like women's rights, environmental issues, healthy food, organic food and sustainability etc. I have a much more detailed customer avatar if required

Font styles to use
Serif
Sans Serif
Decorative
Script

Colors
e8e8e8
474747
1b1b1b
add136

Requirements
Must have
• The label, should look minimalist and modern, throw in some out of the box creativity and we have a winner. Creativity will definitely be of importance. Our packaging is a biodegradable brown paper stand up pouch (Example link in product description). So to make it standout from other colorful packaging - being creative would definitely help.
• Please use the color schemes provided in the brief (See attachments). But if you want to experiment I would be open to it, as long as they are still minimalist and does not stray very far from the color given in the brief :)

```html
<!DOCTYPE html>
<html lang="en">
<head>
<meta charset="utf-8">
<title>Bloom Within – Label Sizes</title>
<link rel="stylesheet" href="https://fonts.googleapis.com/css2?family=Jost:wght@300;400;500;600;700&display=swap">
<style>
  :root {
    --canvas: #e7e8e9;
    --paper: #ffffff;
    --ink: #111111;
    --mint: #72c796;
  }
  * { margin: 0; padding: 0; box-sizing: border-box; }
  html, body { width: 1200px; height: 1200px; overflow: hidden; background: var(--canvas); }
  body { position: relative; font-family: "Jost", Arial, sans-serif; color: var(--ink); }

  .label {
    position: absolute;
    width: 364px;
    height: 486px;
    background: var(--paper);
    border-radius: 12px;
    overflow: hidden;
    transform-origin: 0 0;
  }
  .label--500 { left: 236px; top: 357px; }
  .label--300 { left: 707px; top: 478px; transform: scale(0.74, 0.75); }

  .brand-name {
    position: absolute;
    left: 51px;
    top: 217px;
    transform: translate(-50%, -50%) rotate(-90deg);
    font-size: 53px;
    font-weight: 400;
    letter-spacing: 21px;
    text-indent: 21px;
    line-height: 1;
    white-space: nowrap;
  }

  .title-main {
    position: absolute;
    left: 109px;
    top: 128px;
    font-size: 70px;
    font-weight: 700;
    letter-spacing: -2px;
    line-height: 1;
    white-space: nowrap;
  }
  .title-sub {
    position: absolute;
    left: 114px;
    top: 199px;
    font-size: 44px;
    font-weight: 700;
    color: var(--mint);
    letter-spacing: 0.5px;
    line-height: 1;
    white-space: nowrap;
  }
  .title-rule {
    position: absolute;
    left: 111px;
    top: 256px;
    width: 219px;
    border-top: 1px solid var(--ink);
  }
  .tagline {
    position: absolute;
    left: 111px;
    top: 262px;
    font-size: 10px;
    font-weight: 500;
    letter-spacing: -0.2px;
    white-space: nowrap;
  }

  .ingredients {
    position: absolute;
    left: 111px;
    top: 296px;
    width: 198px;
    list-style: none;
  }
  .ingredients li {
    height: 22.5px;
    border-bottom: 1px solid var(--ink);
    font-size: 12.5px;
    font-weight: 300;
    line-height: 22px;
    white-space: nowrap;
  }
  .ingredients .sep {
    display: inline-block;
    width: 1px;
    height: 14px;
    background: var(--ink);
    margin: 0 12px;
    vertical-align: -2px;
  }

  .category {
    position: absolute;
    left: 111px;
    top: 403px;
    font-size: 11.5px;
    font-weight: 600;
    letter-spacing: 0.2px;
  }

  .footer {
    position: absolute;
    left: 0;
    top: 431px;
    width: 100%;
    height: 55px;
    border-top: 1px solid var(--ink);
  }
  .net-weight {
    position: absolute;
    left: 52px;
    top: 15px;
    transform: translateX(-50%);
    text-align: center;
    font-size: 11.5px;
    font-weight: 300;
    line-height: 14px;
    white-space: nowrap;
  }
  .badges { position: absolute; left: 0; top: 0; }
</style>
</head>
<body>

  <section class="label label--500">
    <div class="brand-name">ORAVELLE</div>
    <h1 class="title-main">BLOOM</h1>
    <h2 class="title-sub">WITHIN</h2>
    <div class="title-rule"></div>
    <p class="tagline">Organic Prebiotics And Superfood Blend For Women</p>
    <ul class="ingredients">
      <li>Baobab<span class="sep"></span>Flaxseed</li>
      <li>Acai Berry<span class="sep"></span>Maca Powder</li>
      <li>Goji Berry<span class="sep"></span>Aronia Berry</li>
      <li>Camu Camu<span class="sep"></span>Cinnamon</li>
    </ul>
    <p class="category">FOOD SUPPLEMENT</p>
    <div class="footer">
      <p class="net-weight">Net Weight<br>500 gm</p>
      <svg class="badges" width="364" height="55" viewBox="0 0 364 55" role="img" aria-label="Certification badges">
        <g fill="none" stroke="#111" stroke-width="2">
          <circle cx="135" cy="27" r="14"/>
          <circle cx="174" cy="27" r="14"/>
          <circle cx="213" cy="27" r="14"/>
          <circle cx="255" cy="26" r="16" stroke-width="1.2"/>
          <circle cx="302" cy="26" r="16" stroke-width="1.2"/>
        </g>
      </svg>
    </div>
  </section>

  <section class="label label--300">
    <div class="brand-name">ORAVELLE</div>
    <h1 class="title-main">BLOOM</h1>
    <h2 class="title-sub">WITHIN</h2>
    <div class="title-rule"></div>
    <p class="tagline">Organic Prebiotics And Superfood Blend For Women</p>
    <ul class="ingredients">
      <li>Baobab<span class="sep"></span>Flaxseed</li>
      <li>Acai Berry<span class="sep"></span>Maca Powder</li>
      <li>Goji Berry<span class="sep"></span>Aronia Berry</li>
      <li>Camu Camu<span class="sep"></span>Cinnamon</li>
    </ul>
    <p class="category">FOOD SUPPLEMENT</p>
    <div class="footer">
      <p class="net-weight">Net Weight<br>300 gm</p>
      <svg class="badges" width="364" height="55" viewBox="0 0 364 55" role="img" aria-label="Certification badges">
        <g fill="none" stroke="#111" stroke-width="2">
          <circle cx="135" cy="27" r="14"/>
          <circle cx="174" cy="27" r="14"/>
          <circle cx="213" cy="27" r="14"/>
          <circle cx="255" cy="26" r="16" stroke-width="1.2"/>
          <circle cx="302" cy="26" r="16" stroke-width="1.2"/>
        </g>
      </svg>
    </div>
  </section>

</body>
</html>
```